Torvane Email Signature Banners – Fabrication Capability Series

www.Torvane.com.au is an Australian engineering and fabrication company specialising in fabrication and welding of :
steel piping spools,
skids and frames,
small volume process steel tanks
and general steel fabrication
We require four distinct banner designs for use in Microsoft Lintaro email signatures. Each banner will highlight a specific capability while maintaining a consistent brand identity.
Deliverables
Four banners total:
Piping Spools Fabrication – focus on precision welding and stainless steel pipework
Skid & Frames Fabrication – highlight skid systems and structural frames
Small Steel Tanks Fabrication – show fabricated tanks and workshop craftsmanship
General Fabrication Solutions – broad steel fabrication theme for company-wide use
Dimensions: 600–700 px wide × 100 px high
Format: PNG (preferred), small file size prefered
Resolution: 72 dpi
Background: non-transparent, industrial or workshop setting
Text examples:
1. Piping Spools Fabrication
Option A: “Expert Fabrication Solutions for Process Piping”
Option B: “Precision Welding for Complex Systems”
Option C: “Delivering Quality in Every Spool”
Option D: “Engineered for Flow, Built for Strength”
2. Skid & Frames Fabrication
Option A: “Custom Engineered Modular Systems”
Option B: “Built Strong. Designed Smart.”
Option C: “Reliable Frames for Industrial Performance”
Option D: “Modular Fabrication for Seamless Integration”
3. Small Steel Tanks Fabrication
Option A: “Precision Built for Your Needs”
Option B: “Compact Strength. Proven Durability.”
Option C: “Fabricated for Performance and Longevity”
Option D: “Small Tanks. Big Reliability.”
4. General Fabrication Solutions
Option A: “Quality Craftsmanship, Proven Results”
Option B: “Your Partner in Precision Fabrication”
Option C: “Engineering Excellence in Every Weld”
Option D: “Australian Fabrication. Global Standards.”
Style Direction
Clean, professional, and engineering‑focused
Use Torvane brand colours
Blend photo realism with vector clarity (no heavy gradients)
Include subtle industrial textures or workshop imagery
Typography: bold sans‑serif, legible at small scale
Usage Context
These banners will appear at the bottom of staff email signatures via Lintaro Email Signature Tool for Microsoft 365, so clarity and fast loading are essential. No Logo is required in the banners.
Reference
Existing Torvane signature is attached. Colour palette to match the signature style and logo.
Target Market(s)
Engineering and construction companies,
Industry/Entity Type
Engineering fabrication design
Look and feel

```html
<!DOCTYPE html>
<html lang="en">
<head>
<meta charset="utf-8">
<title>Piping Spools Fabrication – Email Signature Banner</title>
<link rel="stylesheet" href="https://fonts.googleapis.com/css2?family=Poppins:wght@500;700&display=swap">
<style>
  :root {
    --blue-deep: #1388d2;
    --blue-main: #1e9be2;
    --blue-light: #3fb2ef;
    --white: #ffffff;
  }
  html, body {
    margin: 0;
    padding: 0;
    width: 1200px;
    height: 171px;
    overflow: hidden;
    background: var(--white);
  }
  .banner {
    position: relative;
    width: 1200px;
    height: 171px;
    overflow: hidden;
    background:
      linear-gradient(115deg, transparent 0 55%, rgba(255,255,255,0.07) 55% 68%, transparent 68% 100%),
      linear-gradient(115deg, transparent 0 30%, rgba(255,255,255,0.05) 30% 42%, transparent 42% 100%),
      linear-gradient(90deg, var(--blue-deep) 0%, var(--blue-main) 50%, var(--blue-light) 100%);
    font-family: "Poppins", sans-serif;
    color: var(--white);
  }
  .banner__art {
    position: absolute;
    inset: 0;
    width: 1200px;
    height: 171px;
  }
  .banner__copy {
    position: absolute;
    left: 440px;
    width: 720px;
    top: 0;
    height: 171px;
    text-align: center;
  }
  .banner__headline {
    position: absolute;
    left: 0;
    right: 0;
    top: 44px;
    margin: 0;
    font-weight: 700;
    font-size: 34px;
    line-height: 1;
    white-space: nowrap;
  }
  .banner__rule {
    position: absolute;
    left: 205px;
    width: 303px;
    top: 97px;
    height: 2px;
    background: var(--white);
  }
  .banner__service {
    position: absolute;
    left: 0;
    right: 0;
    top: 113px;
    margin: 0;
    font-weight: 500;
    font-size: 24px;
    line-height: 1;
    white-space: nowrap;
  }
</style>
</head>
<body>
  <div class="banner">
    <svg class="banner__art" viewBox="0 0 1200 171" xmlns="http://www.w3.org/2000/svg">
      <defs>
        <linearGradient id="photoTone" x1="0" y1="0" x2="1" y2="1">
          <stop offset="0" stop-color="#8fa6b3"/>
          <stop offset="0.55" stop-color="#6f8796"/>
          <stop offset="1" stop-color="#2f4350"/>
        </linearGradient>
      </defs>
      <polygon class="chevron-frame" points="0,0 366,0 414,85.5 366,171 0,171" fill="var(--white)"/>
      <polygon class="chevron-photo" role="img"
        aria-label="Welder in protective gear welding a large stainless steel pipe spool in a workshop"
        points="0,0 352,0 399,85.5 352,171 0,171" fill="url(#photoTone)"/>
      <polygon class="chevron-edge" points="372,0 382,0 428,85.5 382,171 372,171 418,85.5"
        fill="var(--blue-deep)" opacity="0.6"/>
    </svg>
    <div class="banner__copy">
      <h1 class="banner__headline">Precision Welding for Complex System</h1>
      <div class="banner__rule"></div>
      <p class="banner__service">Piping Spools Fabrication</p>
    </div>
  </div>
</body>
</html>
```